Business Card Re-Design/Update

We'd like to update out business cards. I've included our current "Style guide" which has the colour scheme of the organisation in it. I've also included the branding files with logos etc in them.

I've also included a copy of one of our existing cards so that you can see how ugly/dated they look. I'd like a fresh modern corporate look.

Target Market(s)

These are for our clients, potential clients, industry contacts - like all business cards

Contact Information for Business Card

Name
Position
Company Address - Level 1, 47 Fernby Street, Carlow Qld 4072
Direct Phone
mobile
Email
Website -www.korvalit.com.au
Logo

Colors

Designer to choose colors to be used in the design.

Requirements
Must have
• Main Logo
• Cards will need to be editable to be able to personalize them for each new employee.
Nice to have
• The MapOut, ShipWell, KeepSteady would be okay to have if they can be sensibly and professionally added to the look without detracting from the main imagery.
• Maybe they could go on the back of the card? will leave this to your creative discretion as to whether/where they fit.
Should not have
• Should not have decorative or script fonts

```html
<!DOCTYPE html>
<html lang="en">
<head>
<meta charset="utf-8">
<title>korvalit business card</title>
<link rel="stylesheet" href="https://fonts.googleapis.com/css2?family=Questrial&family=Roboto:wght@400;500&display=swap">
<style>
  :root {
    --backdrop: #8c8c8c;
    --card-white: #f3f3f3;
    --card-back-white: #ffffff;
    --charcoal: #37373a;
    --ink: #2b2b2b;
    --brand-red: #d71920;
    --rule: #555555;
    --ship-blue: #1e88c9;
    --keep-magenta: #b5198f;
    --map-green: #5aa83c;
  }
  * { margin: 0; padding: 0; box-sizing: border-box; }
  html, body { width: 1200px; height: 1200px; overflow: hidden; }
  body {
    background: var(--backdrop);
    position: relative;
    font-family: "Roboto", Arial, sans-serif;
    color: var(--ink);
  }
  .card { position: absolute; top: 310px; height: 594px; overflow: hidden; }

  /* Front */
  .card-front { left: 234px; width: 364px; background: var(--card-white); text-align: center; }
  .brand-square {
    position: absolute; left: 162px; top: 398px; width: 40px; height: 40px;
    background: var(--brand-red);
  }
  .brand-square { top: 88px; }
  .brand-name {
    position: absolute; left: 0; right: 0; top: 162px;
    font-family: "Questrial", Arial, sans-serif; font-size: 56px; line-height: 1;
    color: var(--charcoal); letter-spacing: 0.5px;
  }
  .person-name {
    position: absolute; left: 0; right: 0; top: 305px;
    font-family: "Questrial", Arial, sans-serif; font-size: 22px; font-weight: 700;
    color: var(--brand-red); letter-spacing: 0.3px;
  }
  .person-role { position: absolute; left: 0; right: 0; top: 331px; font-size: 16.5px; }
  .icon-row { position: absolute; left: 60px; top: 368px; width: 245px; height: 22px; }
  .contact-list {
    position: absolute; left: 0; right: 0; top: 396px;
    list-style: none; font-size: 16.5px; line-height: 21.3px;
  }
  .divider {
    position: absolute; left: 60px; width: 245px; top: 511px;
    border-top: 1px solid var(--rule);
  }
  .address { position: absolute; left: 0; right: 0; top: 520px; font-size: 16.5px; line-height: 21px; font-style: normal; }

  /* Back */
  .card-back { left: 627px; width: 370px; background: var(--card-back-white); }
  .back-band { position: absolute; left: 0; top: 0; width: 370px; height: 245px; background: var(--charcoal); }
  .back-brand {
    position: absolute; left: 0; right: 0; top: 92px; text-align: center;
    font-family: "Questrial", Arial, sans-serif; font-size: 58px; line-height: 1;
    color: var(--brand-red);
  }
  .service {
    position: absolute; display: flex; align-items: center; gap: 9px;
    font-family: "Questrial", Arial, sans-serif; font-size: 30px; font-weight: 700; line-height: 1;
  }
  .service-mark { width: 24px; height: 24px; display: block; }
  .service-ship { left: 40px; top: 444px; color: var(--ship-blue); }
  .service-ship .service-mark { background: var(--ship-blue); }
  .service-keep { left: 98px; top: 484px; color: var(--keep-magenta); }
  .service-keep .service-mark { background: var(--keep-magenta); }
  .service-map { left: 170px; top: 528px; color: var(--map-green); }
  .service-map .service-mark { background: var(--map-green); }
</style>
</head>
<body>
  <section class="card card-front">
    <div class="brand-square"></div>
    <div class="brand-name">korvalit</div>
    <div class="person-name">MAREN HOLT</div>
    <div class="person-role">Business Development Manager</div>
    <svg class="icon-row" viewBox="0 0 245 22" aria-hidden="true">
      <line x1="0" y1="11" x2="64" y2="11" stroke="#333" stroke-width="1.2"/>
      <line x1="181" y1="11" x2="245" y2="11" stroke="#333" stroke-width="1.2"/>
      <g fill="#d71920">
        <rect x="66" y="1" width="20" height="20" rx="2"/>
        <rect x="89" y="1" width="20" height="20" rx="2"/>
        <rect x="112" y="1" width="20" height="20" rx="2"/>
        <rect x="135" y="1" width="20" height="20" rx="2"/>
        <rect x="158" y="1" width="20" height="20" rx="2"/>
      </g>
      <g fill="none" stroke="#fff" stroke-width="1.6" stroke-linecap="round" stroke-linejoin="round">
        <path d="M71 6 l3 0 l1 3 l-2 1.5 q1.5 3 4 4 l1.5 -2 l3 1 l0 3 q-8 0 -10.5 -10.5z"/>
        <rect x="95" y="5" width="8" height="12" rx="1"/>
        <line x1="98" y1="14.5" x2="100" y2="14.5"/>
        <rect x="117" y="5" width="10" height="4"/>
        <rect x="115" y="9" width="14" height="6"/>
        <rect x="118" y="13" width="8" height="4"/>
        <rect x="139" y="6" width="12" height="10"/>
        <path d="M139 6 l6 5 l6 -5"/>
        <circle cx="168" cy="11" r="6"/>
        <path d="M162 11 h12 M168 5 q-3 6 0 12 M168 5 q3 6 0 12"/>
      </g>
    </svg>
    <ul class="contact-list">
      <li>+61 (0)400 555 018</li>
      <li>+61 (0)7 5550 1234</li>
      <li>+61 (0)7 5550 1299</li>
      <li>mholt@korvalit.com.au</li>
      <li>www.korvalit.com.au</li>
    </ul>
    <div class="divider"></div>
    <address class="address">Level 1, 47 Fernby Street<br>Carlow Qld 4072</address>
  </section>

  <section class="card card-back">
    <div class="back-band"></div>
    <div class="back-brand">korvalit</div>
    <div class="service service-ship"><span class="service-mark"></span>ShipWell</div>
    <div class="service service-keep"><span class="service-mark"></span>KeepSteady</div>
    <div class="service service-map"><span class="service-mark"></span>MapOut</div>
  </section>
</body>
</html>
```